lantern pathway for children needs a website designer

We need a website designer for our new extension to our company known as 'lantern pathway' providing shadow support services to children based in Singapore. We are a sister branch of a private clinic 'Kindred Bridge' providing speech language, occupational, and educational therapy to children.

We would like to use our own photos. So the selected design should have a frame with pictures to give us an idea but we will replace them with our own. We will be needing help with inputting information and changing information throughout.

We would like to see designs that are simple, and professional. We have a logo (see attached). The result should convey professionalism in shadow support, fostering independent thinking and moving students towards self-learning.

Target Market(s)

Teachers, psychologists, parents

Industry/Entity Type

Clinic

Requirements
Should not have
• too distracting colours

```html
<!DOCTYPE html>
<html lang="en">
<head>
<meta charset="utf-8">
<title>Lantern Pathway – Shadow Support</title>
<link href="https://fonts.googleapis.com/css2?family=Open+Sans:wght@400;600;700&display=swap" rel="stylesheet">
<style>
:root{
  --brand:#8b0a0a;
  --text:#444;
  --heading:#222;
  --rule:#cfcfcf;
  --btn:#e2e2e2;
  --footer:#414141;
  --hero-a:#e06a60;
  --hero-b:#f0a08f;
  --hero-c:#f6c3b0;
}
*{box-sizing:border-box;margin:0;padding:0}
html,body{width:1024px;height:1200px;overflow:hidden;background:#fff}
body{position:relative;font-family:'Open Sans',Arial,sans-serif;color:var(--text);font-size:10px}

/* header */
.site-header{position:absolute;left:0;top:0;width:1024px;height:82px;background:#fff}
.brand{position:absolute;left:114px;top:26px;display:flex;align-items:center;gap:8px;font-size:27px;font-weight:700;color:var(--brand);letter-spacing:-.3px}
.brand-dot{width:20px;height:20px;border-radius:50%;background:var(--brand)}
.topbar{position:absolute;right:118px;top:4px;display:flex;align-items:center;gap:12px;font-size:11px}
.phone{color:#888;display:flex;align-items:center;gap:4px}
.account a{color:var(--brand);text-decoration:none}
.main-nav{position:absolute;right:118px;top:53px;display:flex;font-size:11px}
.main-nav a{color:#222;text-decoration:none;padding:0 16px;border-left:1px solid #ccc;line-height:14px}
.main-nav a:first-child{border-left:none}
.main-nav a.active{color:var(--brand);border-bottom:2px solid var(--brand);padding-bottom:4px}

/* hero */
.hero{position:absolute;left:0;top:82px;width:1024px;height:303px;background:linear-gradient(100deg,var(--hero-a) 0%,var(--hero-b) 55%,var(--hero-c) 100%)}
.hero-title{position:absolute;left:0;width:1024px;top:104px;text-align:center;font-size:29px;font-weight:600;color:#fff;text-shadow:1px 2px 3px rgba(0,0,0,.35);letter-spacing:-.3px}
.hero-photo{position:absolute;left:124px;top:167px;width:780px;height:278px;background:linear-gradient(180deg,#dceaf4 0%,#c9d8c6 40%,#a8c45a 80%,#7ea43a 100%)}
.slider-arrow{position:absolute;top:282px;font-size:26px;color:#555;font-weight:700}
.hero-shadow{position:absolute;left:80px;top:446px;width:864px;height:26px}

/* sections */
.section-title{position:absolute;left:113px;width:798px;text-align:center;font-size:19px;color:var(--heading);font-weight:400}
.section-title span{background:#fff;padding:0 26px;position:relative}
.section-title::before{content:"";position:absolute;left:0;right:0;top:50%;border-top:1px solid var(--rule)}
.body-copy{position:absolute;text-align:center;line-height:14.4px;font-size:10px}
.btn{position:absolute;background:var(--btn);color:#444;font-size:10px;padding:2px 7px;line-height:13px}
.card-icon{position:absolute;width:50px;height:50px;border-radius:50%;background:#f1e3e3;display:flex;align-items:center;justify-content:center}
.card-icon i{width:38px;height:38px;border-radius:50%;background:var(--brand);display:flex;align-items:center;justify-content:center}
.card-title{position:absolute;width:288px;text-align:center;color:var(--brand);font-size:12px;font-weight:400}
.service-photo{position:absolute;width:175px;height:73px}

/* footer */
.site-footer{position:absolute;left:0;top:1142px;width:1024px;height:41px;background:var(--footer);color:#eee;font-size:10px}
.site-footer p{position:absolute;left:114px;top:13px}
.social{position:absolute;top:9px;width:22px;height:22px;border-radius:50%;background:#5a5a5a}
</style>
</head>
<body>

<header class="site-header">
  <div class="brand"><span class="brand-dot"></span>Lantern Pathway</div>
  <div class="topbar">
    <span class="phone">
      <svg width="10" height="13" viewBox="0 0 10 13"><path d="M2 1 L4 1 L5 4 L3.5 5 Q4.5 8 6.5 9 L7.5 7.8 L9.5 9.5 L8.5 12 Q1 11 1 2 Z" fill="#8b0a0a"/></svg>
      065 6100 2040
    </span>
    <span class="account"><a href="#">Register</a> | <a href="#">Login</a></span>
  </div>
  <nav class="main-nav">
    <a href="#" class="active">Home</a><a href="#">About Us</a><a href="#">Services</a><a href="#">Shadow Support</a><a href="#">For Referrers</a><a href="#">Contact Us</a>
  </nav>
</header>

<section class="hero"></section>
<h1 class="hero-title">Welcome To Lantern Pathway</h1>
<div class="hero-photo" role="img" aria-label="Photo of smiling children lying on grass"></div>
<span class="slider-arrow" style="left:98px">&#10094;</span>
<span class="slider-arrow" style="left:912px">&#10095;</span>
<svg class="hero-shadow" viewBox="0 0 864 26" preserveAspectRatio="none">
  <defs><radialGradient id="shade" cx="50%" cy="0%" r="50%"><stop offset="0" stop-color="#999"/><stop offset="1" stop-color="#fff" stop-opacity="0"/></radialGradient></defs>
  <path d="M0 0 H864 Q432 40 0 0Z" fill="url(#shade)"/>
</svg>

<h2 class="section-title" style="top:480px"><span>ABOUT US</span></h2>
<p class="body-copy" style="left:118px;width:790px;top:514px">Lantern Pathway is part of the Kindred Bridge Group of Companies, who are providing speech language therapy, occupational therapy and educational therapy services to both the Singapore and the international school community.</p>
<p class="body-copy" style="left:114px;width:798px;top:557px">Lantern Pathway was borne out of our Speech language Pathologists’ frustration at a frequent lack of carry-over of goals to a classroom setting by external shadows. Carrying over of goals in real settings is highly important as it allows for students to generalize skills quicker. &nbsp;By generalizing skills, this means that the student would have truly learned a specific skill and can apply this in different settings.</p>
<span class="btn" style="left:482px;top:613px">Read More</span>

<h2 class="section-title" style="top:665px"><span>SHADOW SUPPORT</span></h2>

<div class="card-icon" style="left:200px;top:712px"><i><svg width="18" height="18" viewBox="0 0 18 18"><circle cx="7" cy="11" r="4" fill="none" stroke="#fff" stroke-width="2.5" stroke-dasharray="2 1.2"/><circle cx="13" cy="5" r="2.5" fill="none" stroke="#fff" stroke-width="2" stroke-dasharray="1.5 1"/></svg></i></div>
<div class="card-icon" style="left:489px;top:712px"><i><svg width="16" height="16" viewBox="0 0 16 16"><path d="M8 2 L14 8 H10 V14 H6 V8 H2 Z" fill="#fff"/></svg></i></div>
<div class="card-icon" style="left:777px;top:712px"><i><svg width="16" height="16" viewBox="0 0 16 16"><path d="M3 8 L7 12 L13 4" fill="none" stroke="#fff" stroke-width="2.4"/></svg></i></div>

<h3 class="card-title" style="left:80px;top:772px">What is shadow support?</h3>
<h3 class="card-title" style="left:368px;top:772px">What are its Advantages?</h3>
<h3 class="card-title" style="left:658px;top:769px">How do I know if my child needs shadowing?</h3>

<p class="body-copy" style="left:114px;width:222px;top:794px">Lantern Pathway is part of the Kindred Bridge Group of Companies, who are providing speech language therapy, occupational therapy and educational therapy..</p>
<p class="body-copy" style="left:402px;width:222px;top:794px">Lantern Pathway is part of the Kindred Bridge Group of Companies, who are providing speech language therapy, occupational therapy and educational therapy..</p>
<p class="body-copy" style="left:690px;width:222px;top:794px">Lantern Pathway is part of the Kindred Bridge Group of Companies, who are providing speech language therapy, occupational therapy and educational therapy..</p>

<span class="btn" style="left:194px;top:867px">Read More</span>
<span class="btn" style="left:482px;top:867px">Read More</span>
<span class="btn" style="left:770px;top:867px">Read More</span>

<h2 class="section-title" style="top:920px"><span>OUR SERVICES</span></h2>

<div class="service-photo" style="left:142px;top:962px;background:linear-gradient(90deg,#c96a2a 0%,#3a2f28 35%,#d9d0c2 60%,#b84a3a 100%)" role="img" aria-label="Photo of a therapist training a shadow"></div>
<div class="service-photo" style="left:429px;top:962px;background:linear-gradient(180deg,#dfe7d8 0%,#c9b49a 55%,#8fae5a 100%)" role="img" aria-label="Photo of a smiling family outdoors"></div>
<div class="service-photo" style="left:715px;top:962px;background:linear-gradient(90deg,#3d4a6a 0%,#b9c4cf 45%,#8a6a4a 75%,#2e3b5e 100%)" role="img" aria-label="Photo of educators working with students in a classroom"></div>

<h3 class="card-title" style="left:85px;top:1042px">Train shadows</h3>
<h3 class="card-title" style="left:373px;top:1042px">Provide families</h3>
<h3 class="card-title" style="left:659px;top:1042px">Work with educational</h3>

<p class="body-copy" style="left:114px;width:228px;top:1066px">Train shadows with a strong focus on equipping them with dynamic, clinical skills.</p>
<p class="body-copy" style="left:400px;width:228px;top:1066px">Provide families with well-trained Shadows who are mentored by Speech Language Pathologists and Professional Therapists to carry out shadow support.</p>
<p class="body-copy" style="left:686px;width:228px;top:1066px">Work with educational professionals (Educational Psychologists) to provide an effective solution to the learning needs of a student.</p>

<footer class="site-footer">
  <p>Copyright © 2014 Lantern Pathway, All Rights Reserved</p>
  <span class="social" style="left:853px" aria-label="Social link"></span>
  <span class="social" style="left:881px" aria-label="Social link"></span>
</footer>

</body>
</html>
```